Harborview Estates Business Card for Apartment Buildings

Create business cards for resident managers who run apartment buildings. The audience is the public who are searching for apartment rentals, and current residents who live at the apartment building. Key design element will be incorporating the company logo, however, the logo cannot dominate. The building name and manager name are more important than the logo. Current business card design leaves little room for copy, so we may need to reduce the size on the current card to allow for more space for copy.

Target Market(s)

Adults 18-65 years of age, who are looking for an apartment rental, plus current residents who live at our apartment buildings.

Industry/Entity Type

Property Management

Contact Information for Business Card

A major design element will be use of the company logo. Important property and manager contact information must be part of the design. The size of the logo will need to be reduced to make room for building and manager contact copy.

Font styles to use
Sans Serif

Colors
3176b5
000000
959595
ffffff

Requirements
Must have
• 1) Incorporate the company logo.
• 2) Use the company colors (dark blue, black/grey, over white).
• 3) FEATURE THE BUILDING NAME
• 4) FEATURE THE MANAGER NAME
• 5) The company name is less important than BUILDING and MANAGER
• 6) Manager contact information
• **SEE ATTACHED CREATIVE BRIEF**
Nice to have
• 1) Back of card logo watermark
• 2) Ability to write notes on back of carfd
Should not have
• Avoid letting the company logo dominate the card, the building name and manager are more important than the company logo.

```html
<!DOCTYPE html>
<html lang="en">
<head>
<meta charset="utf-8">
<title>Harborview Estates – Resident Manager Business Card</title>
<link rel="stylesheet" href="https://fonts.googleapis.com/css2?family=Roboto:wght@400;500;700&family=Roboto+Condensed:wght@500;700&display=swap">
<style>
  :root {
    --brand-blue: #0f6ca8;
    --ink: #3f3f3f;
    --grey: #959595;
    --paper: #f4f4f4;
    --white: #ffffff;
    --stage: #2b2b2b;
  }
  * { margin: 0; padding: 0; box-sizing: border-box; }
  html, body { width: 1200px; height: 960px; overflow: hidden; }
  body {
    background: var(--stage);
    font-family: "Roboto", Arial, sans-serif;
    position: relative;
  }
  .card {
    position: absolute;
    left: 320px;
    width: 600px;
    height: 344px;
  }
  .card-front { top: 100px; background: var(--paper); color: var(--ink); }
  .card-back { top: 492px; background: var(--brand-blue); color: var(--white); }

  .brand {
    position: absolute;
    display: flex;
    align-items: center;
    gap: 9px;
    font-weight: 700;
    text-transform: uppercase;
    letter-spacing: 1px;
    white-space: nowrap;
  }
  .brand-mark { display: block; border-radius: 50%; flex: none; }
  .card-front .brand {
    top: 72px; left: 0; right: 0; justify-content: center;
    color: var(--grey); font-size: 18px;
  }
  .card-front .brand-mark { width: 22px; height: 22px; background: var(--grey); }

  .manager-name {
    position: absolute; top: 178px; left: 0; right: 0;
    text-align: center;
    font-family: "Roboto Condensed", Arial, sans-serif;
    font-weight: 700; font-size: 25px;
    color: var(--brand-blue);
  }
  .title-rule {
    position: absolute; top: 209px; left: 47px; right: 47px;
    display: flex; align-items: center; gap: 8px;
    font-family: "Roboto", Arial, sans-serif;
    font-weight: 500; font-size: 15px; color: var(--ink);
  }
  .title-rule::before, .title-rule::after {
    content: ""; flex: 1; height: 1px; background: #555;
  }

  .property {
    position: absolute; top: 241px; left: 47px;
    font-style: normal;
    font-size: 14px; line-height: 19px; color: var(--ink);
  }
  .property-name {
    font-family: "Roboto", Arial, sans-serif;
    font-weight: 700; font-size: 16px; line-height: 20px; color: var(--brand-blue);
  }
  .property-web { letter-spacing: 1.4px; margin-top: 1px; }

  .contacts {
    position: absolute; top: 244px; right: 44px;
    list-style: none; font-size: 14px; line-height: 19.5px; color: var(--ink);
  }
  .contacts li { display: flex; align-items: center; justify-content: flex-end; gap: 11px; }
  .contacts svg { width: 14px; height: 14px; fill: var(--brand-blue); flex: none; }

  .card-back .brand {
    top: 242px; right: 36px; color: var(--white); font-size: 20px;
  }
  .card-back .brand-mark { background: var(--white); width: 22px; height: 22px; }
  .tagline {
    position: absolute; top: 291px; right: 36px;
    font-weight: 700; font-size: 14px; color: var(--white);
  }
</style>
</head>
<body>
  <section class="card card-front">
    <div class="brand"><span class="brand-mark"></span>Harborview Estates LLC</div>
    <h1 class="manager-name">Marisol Delgado</h1>
    <div class="title-rule">Resident Manager</div>

    <address class="property">
      <div class="property-name">Cedar Court Apartments</div>
      <div>1425 Linden Avenue</div>
      <div>Lakemont, CA 91820</div>
      <div class="property-web">www.harborviewest.com</div>
    </address>

    <ul class="contacts">
      <li>555-201-4470
        <svg viewBox="0 0 16 16" aria-label="Office phone"><path d="M3.5 1.5l2.3-.4 1.4 3.2-1.5 1.1c.8 1.8 2.1 3.1 3.9 3.9l1.1-1.5 3.2 1.4-.4 2.3c-.2.9-1 1.5-1.9 1.4C6.5 12.4 3.6 9.5 2.1 3.4 1.9 2.5 2.6 1.7 3.5 1.5z"/></svg></li>
      <li>555-310-8824
        <svg viewBox="0 0 16 16" aria-label="Mobile"><path d="M5 1h6a1 1 0 0 1 1 1v12a1 1 0 0 1-1 1H5a1 1 0 0 1-1-1V2a1 1 0 0 1 1-1zm.5 1.5v9.5h5V2.5zM8 12.8a.8.8 0 1 0 0 1.6.8.8 0 0 0 0-1.6z"/></svg></li>
      <li>555-642-1190
        <svg viewBox="0 0 16 16" aria-label="Fax"><path d="M4 1h8v4H4zM2 6h12a1 1 0 0 1 1 1v5h-2.5v3h-9v-3H1V7a1 1 0 0 1 1-1zm3.5 5v2.5h5V11z"/></svg></li>
      <li>marisol@harborviewest.com
        <svg viewBox="0 0 16 16" aria-label="Email"><path d="M1 3.5h14v1.2L8 9 1 4.7zM1 6.2l7 4.3 7-4.3v6.3H1z"/></svg></li>
    </ul>
  </section>

  <section class="card card-back">
    <div class="brand"><span class="brand-mark"></span>Harborview Estates LLC</div>
    <p class="tagline">Multifamily Property Management</p>
  </section>
</body>
</html>
```